Meadowlark Property Review is a leading provider of residential appraisal and home inspection products in S

I need a business card/logo designed that obviously describes my business. We are a residential appraisal and home inspection company in Springfield, MO. We offer residential appraisals, home inspection, pest inspection and radon gas measurement. We have been in business for 18 years and hold state certified residential appraisal licenses and OBREX certified home inspection licenses. I have a logo that I really like and will attach, but would be open to new suggestions. I like more modern designs than traditional and would like a two sided card with our services, licenses and qualifications on the back.

```html
<!DOCTYPE html>
<html lang="en">
<head>
<meta charset="utf-8">
<title>Meadowlark Property Review — Business Card</title>
<link href="https://fonts.googleapis.com/css2?family=Open+Sans:wght@400;600;700&display=swap" rel="stylesheet">
<style>
  :root {
    --orange: #f39325;
    --orange-soft: #f7b25a;
    --brown: #8c6a3f;
    --ink: #2b2b2b;
    --paper: #ffffff;
    --backdrop: #ece7e0;
  }
  * { box-sizing: border-box; margin: 0; padding: 0; }
  html, body { width: 1200px; height: 913px; overflow: hidden; }
  body {
    background: var(--backdrop);
    font-family: "Open Sans", Arial, sans-serif;
    color: var(--ink);
    display: flex;
    align-items: center;
    justify-content: center;
    gap: 28px;
  }
  .card {
    position: relative;
    width: 560px;
    height: 320px;
    background: var(--paper);
    box-shadow: 0 6px 18px rgba(0,0,0,0.14);
    overflow: hidden;
  }
  .card__band { position: absolute; left: 0; bottom: 0; width: 560px; height: 70px; }

  .brand { display: flex; align-items: center; gap: 8px; }
  .brand__mark { width: 12px; height: 12px; background: var(--orange); flex: none; }
  .brand__name {
    font-weight: 700; font-size: 19px; color: var(--brown);
    line-height: 1.1; width: 150px;
  }

  /* front */
  .front__brand { position: absolute; right: 38px; top: 52px; }
  .front__badge {
    position: absolute; right: 232px; top: 58px;
    width: 34px; height: 34px; border-radius: 50%;
    background: #e8c98a; border: 2px solid #c9a35a;
  }
  .person { position: absolute; left: 40px; top: 80px; }
  .person::before {
    content: ""; position: absolute; left: -14px; top: 4px;
    width: 5px; height: 30px; background: var(--orange);
  }
  .person__name { font-weight: 700; font-size: 22px; letter-spacing: 0.5px; line-height: 1.3; }
  .person__role { font-weight: 600; font-size: 11px; color: var(--orange); letter-spacing: 0.5px; }
  .address { position: absolute; left: 40px; top: 128px; font-size: 12.5px; font-weight: 600; line-height: 1.3; }
  .contact { position: absolute; left: 40px; top: 186px; list-style: none; font-size: 12.5px; font-weight: 600; }
  .contact li { display: flex; align-items: center; gap: 7px; line-height: 1.5; }
  .contact svg { width: 11px; height: 11px; fill: var(--orange); flex: none; }

  /* back */
  .services {
    position: absolute; right: 36px; top: 36px; list-style: none;
    text-align: right; font-size: 11px; letter-spacing: 0.4px; line-height: 1.45;
  }
  .services li { display: flex; justify-content: flex-end; align-items: center; gap: 8px; }
  .services li::after {
    content: ""; width: 7px; height: 7px; border-radius: 50%; background: var(--orange-soft);
  }
  .services li.no-dot::after { background: transparent; }
  .back__brand { position: absolute; left: 40px; top: 156px; }
  .back__brand .brand__name { font-size: 20px; width: auto; white-space: nowrap; }
  .tagline {
    position: absolute; left: 28px; top: 206px; width: 380px;
    font-size: 9.5px; font-weight: 700; line-height: 1.35;
  }
</style>
</head>
<body>

<section class="card card--front" aria-label="Card front">
  <div class="front__badge" role="img" aria-label="Certification badge"></div>
  <div class="brand front__brand">
    <span class="brand__mark"></span>
    <span class="brand__name">Meadowlark Property Review</span>
  </div>

  <div class="person">
    <p class="person__name">JORDAN HALE</p>
    <p class="person__role">OWNER</p>
  </div>
  <p class="address">Meadowlark Property Review<br>4410 W Linden Street Suite C<br>Springfield, MO 65807</p>

  <ul class="contact">
    <li><svg viewBox="0 0 24 24"><path d="M6.6 10.8a15 15 0 0 0 6.6 6.6l2.2-2.2c.3-.3.7-.4 1-.2 1.1.4 2.3.6 3.6.6.6 0 1 .4 1 1V20c0 .6-.4 1-1 1A17 17 0 0 1 3 4c0-.6.4-1 1-1h3.5c.6 0 1 .4 1 1 0 1.3.2 2.5.6 3.6.1.3 0 .7-.2 1z"/></svg>417-555-0142</li>
    <li><svg viewBox="0 0 24 24"><rect x="6" y="1" width="12" height="22" rx="2"/></svg>417-555-0187</li>
    <li><svg viewBox="0 0 24 24"><path d="M2 5h20v14H2z M2 5l10 8 10-8" fill="none" stroke="#f39325" stroke-width="2.5"/></svg>info@meadowlarkreview.com</li>
    <li><svg viewBox="0 0 24 24"><circle cx="12" cy="12" r="10" fill="none" stroke="#f39325" stroke-width="2.5"/><path d="M2 12h20M12 2c3 3 3 17 0 20M12 2c-3 3-3 17 0 20" fill="none" stroke="#f39325" stroke-width="2"/></svg>www.meadowlarkreview.com</li>
  </ul>

  <svg class="card__band" viewBox="0 0 560 70" preserveAspectRatio="none" aria-hidden="true">
    <polygon points="0,34 330,34 350,70 0,70" fill="var(--orange)"/>
    <polygon points="330,34 560,0 560,70 350,70" fill="var(--brown)"/>
    <polygon points="318,34 340,34 360,70 338,70" fill="var(--paper)"/>
  </svg>
</section>

<section class="card card--back" aria-label="Card back">
  <ul class="services">
    <li>APPRAISAL</li>
    <li>HOME INSPECTION</li>
    <li>TERMITE</li>
    <li>RADON</li>
    <li>WELL &amp; SEPTIC INSPECTION</li>
    <li class="no-dot">ENERGY AUDITS</li>
  </ul>

  <div class="brand back__brand">
    <span class="brand__mark"></span>
    <span class="brand__name">Meadowlark Property Review</span>
  </div>

  <p class="tagline">With years of experience behind us, we're prepared to tackle anything from a first Time buyer's starter home or a seasoned buyer purchasing a luxurious dream home</p>

  <svg class="card__band" viewBox="0 0 560 70" preserveAspectRatio="none" aria-hidden="true">
    <polygon points="0,34 330,34 350,70 0,70" fill="var(--brown)"/>
    <polygon points="330,34 560,0 560,70 350,70" fill="var(--orange)"/>
    <polygon points="318,34 340,34 360,70 338,70" fill="var(--paper)"/>
  </svg>
</section>

</body>
</html>
```